Audio/ Video Packaging Design for a Technology company.

We need a packaging design for a bag that is 7" wide and 10" high. The design will be for a new line of audio/video products. We would like to see designs that represent a superior quality product that provides a pure connection. We want the equivalent of a nice retail bag that you would find in a store like Tallow Mart. It should be a maximum of three colors. We really want something sharp, professional and eye catching, not whimsical or cartoonish. I've included a couple of examples below. I don't really like the designs of the bags, but I want you to see examples of what I'm looking for.

The company logo, which is uploaded, should be on the design. The words "audio and video products" should be either underneath the logo or to the side. Also, somewhere on the bag, we would like the words "For a Pure Connection"

The winner of this contest will likely get the opportunity for additional work as we have more products ready to launch.

Target Market(s)

resellers, consumers - men 25-60

Industry/Entity Type

It Company

Requirements
Must have
• It should be a maximum of three colors. We really want something sharp, professional and eye catching, not whimsical or cartoonish
Nice to have
• Eye-catching design. Utilize the entire bag but don't make it too busy.
Should not have
• Whimsical, cartoonish

```html
<!DOCTYPE html>
<html lang="en">
<head>
<meta charset="utf-8">
<title>Veltrix Audio and Video Products – Bag Packaging</title>
<link rel="stylesheet" href="https://fonts.googleapis.com/css2?family=Dosis:wght@500;600&family=Encode+Sans+Condensed:wght@500;600&display=swap">
<style>
  :root {
    --stage: #5d86a8;
    --frame-light: #2c93d3;
    --frame-dark: #1a5b9f;
    --navy: #1c2f6b;
    --ink: #14244f;
    --sky: #bfe0f6;
    --mist: #e8f4fc;
    --white: #ffffff;
  }
  * { box-sizing: border-box; margin: 0; padding: 0; }
  html, body { width: 1200px; height: 787px; overflow: hidden; }
  body {
    background: var(--stage);
    position: relative;
    font-family: "Dosis", sans-serif;
  }
  .bag {
    position: absolute;
    top: 118px;
    width: 429px;
    height: 612px;
    border-radius: 22px;
    background: linear-gradient(90deg, var(--frame-light), var(--frame-dark));
  }
  .bag--front { left: 153px; }
  .bag--back { left: 618px; }

  .bag__window {
    position: absolute;
    left: 21px;
    right: 21px;
    top: 20px;
    bottom: 48px;
    border-radius: 16px 16px 0 0;
    background:
      radial-gradient(ellipse at 50% 48%, var(--white) 0%, var(--mist) 35%, var(--sky) 75%, #7fbde8 100%);
    overflow: hidden;
  }
  .bag--back .bag__window {
    bottom: 36px;
    background:
      radial-gradient(ellipse at 50% 50%, #dfecf5 0%, #cfe4f3 40%, #9fcdee 80%, #6fb2e4 100%);
  }
  .bag__seal {
    position: absolute;
    left: 0; right: 0;
    top: 62px;
    height: 14px;
    border-top: 2px solid rgba(28, 91, 159, .35);
    border-bottom: 2px solid rgba(28, 91, 159, .35);
  }
  .bag__tab {
    position: absolute;
    left: 91px;
    top: 0;
    width: 246px;
    height: 114px;
    border-radius: 0 0 18px 18px;
    background: linear-gradient(180deg, var(--frame-dark), #1e64ab);
  }
  .bag__hang-slot {
    position: absolute;
    left: 72px;
    top: 36px;
    width: 102px;
    height: 21px;
    border-radius: 11px;
    background: var(--white);
  }
  .bag__hang-slot::before {
    content: "";
    position: absolute;
    left: 42px;
    top: -7px;
    width: 18px;
    height: 14px;
    border-radius: 9px 9px 0 0;
    background: var(--white);
  }

  .brand {
    position: absolute;
    left: 0; right: 0;
    top: 136px;
    text-align: center;
  }
  .brand__name {
    display: inline-flex;
    align-items: center;
    gap: 12px;
    font-weight: 600;
    font-size: 50px;
    letter-spacing: 2px;
    color: var(--ink);
    line-height: 1;
  }
  .brand__dot {
    width: 26px;
    height: 26px;
    border-radius: 50%;
    background: var(--frame-light);
  }
  .brand__tagline {
    margin-top: 12px;
    font-weight: 500;
    font-size: 22px;
    color: var(--ink);
  }

  .hero-art {
    position: absolute;
    left: 47px;
    top: 446px;
    width: 332px;
    height: 92px;
    border-radius: 46px;
    background: linear-gradient(90deg, #3aa6e6, var(--frame-dark) 50%, #3aa6e6);
  }

  .bag__footer {
    position: absolute;
    left: 0; right: 0;
    bottom: 0;
    height: 48px;
    display: flex;
    align-items: center;
    justify-content: center;
    font-family: "Encode Sans Condensed", sans-serif;
    color: var(--white);
  }
  .bag__slogan { font-size: 26px; font-weight: 600; }
  .bag--back .bag__footer { height: 36px; gap: 8px; }
  .origin { font-size: 13px; font-weight: 600; letter-spacing: .2px; }
  .cert {
    width: 18px;
    height: 18px;
    border-radius: 50%;
    background: var(--white);
  }
  .cert--square { border-radius: 3px; }
</style>
</head>
<body>

  <section class="bag bag--front" aria-label="Front of bag">
    <div class="bag__window">
      <div class="bag__seal"></div>
      <div class="brand">
        <div class="brand__name"><span class="brand__dot"></span>VELTRIX</div>
        <p class="brand__tagline">Audio and Video Products</p>
      </div>
      <div class="hero-art" role="img" aria-label="Blue three-dimensional chevron arrows converging on a central connector shape"></div>
    </div>
    <div class="bag__tab"><div class="bag__hang-slot"></div></div>
    <footer class="bag__footer"><p class="bag__slogan">For a Pure Connection</p></footer>
  </section>

  <section class="bag bag--back" aria-label="Back of bag">
    <div class="bag__window">
      <div class="bag__seal"></div>
      <div class="brand">
        <div class="brand__name"><span class="brand__dot"></span>VELTRIX</div>
        <p class="brand__tagline">Audio and Video Products</p>
      </div>
    </div>
    <div class="bag__tab"><div class="bag__hang-slot"></div></div>
    <footer class="bag__footer">
      <span class="origin">MADE IN CHINA</span>
      <span class="cert cert--square" aria-label="Conformity mark"></span>
      <span class="cert" aria-label="Recovery mark"></span>
      <span class="cert" aria-label="Recycling mark"></span>
    </footer>
  </section>

</body>
</html>
```